Business Card Design Project

We need a Business Card for an Mechanical Engineering firm in Singapore. The design should be Modern & Technical looking, yet eye catching.

Our company deals in Cutting Tools & Machine Accessories for the Manufacturing Industries such as Oil & Gas, Aero Space, etc... For more information on our Company, you can either email me or view our website www.torvalen.com.sg.

We are trying to revamp our image to give our consumers a fresh new perspective to our company, so we welcome all ideas.

Industry/Entity Type

Business

Requirements
Must have
• Must incorporate New Company Logo into the card as shown in Uploaded file.

```html
<!DOCTYPE html>
<html lang="en">
<head>
<meta charset="utf-8">
<title>Torvalen Tools – Business Card</title>
<link rel="stylesheet" href="https://fonts.googleapis.com/css2?family=Arimo:wght@400;700&display=swap">
<style>
  :root {
    --backdrop: #e9e7e4;
    --card: #ffffff;
    --brand: #7d1b3e;
    --ink: #4a4a4a;
    --ink-soft: #6b6b6b;
    --decor: #ebebeb;
    --on-brand: #ffffff;
  }
  html, body {
    margin: 0;
    width: 1200px;
    height: 798px;
    overflow: hidden;
    background: var(--backdrop);
    font-family: "Arimo", Arial, sans-serif;
  }
  .card {
    position: absolute;
    left: 180px;
    top: 159px;
    width: 840px;
    height: 480px;
    background: var(--card);
    box-shadow: 0 6px 24px rgba(0,0,0,0.12);
    overflow: hidden;
  }
  .card__decor {
    position: absolute;
    left: 330px;
    top: -20px;
    width: 530px;
    height: 470px;
    background: radial-gradient(ellipse at 55% 55%, var(--decor) 0%, rgba(235,235,235,0.6) 45%, rgba(255,255,255,0) 72%);
  }
  .brand {
    position: absolute;
    left: 44px;
    top: 78px;
    display: flex;
    align-items: center;
    gap: 10px;
  }
  .brand__mark {
    width: 22px;
    height: 22px;
    border-radius: 50%;
    background: var(--brand);
  }
  .brand__name {
    font-weight: 700;
    font-size: 24px;
    letter-spacing: 0.5px;
    color: var(--brand);
    text-transform: uppercase;
  }
  .contact-person {
    position: absolute;
    left: 44px;
    top: 140px;
  }
  .contact-person__name {
    margin: 0;
    font-weight: 700;
    font-size: 30px;
    color: var(--ink);
  }
  .contact-person__mobile {
    margin: 4px 0 0;
    font-size: 15px;
    color: var(--ink-soft);
  }
  .info-band {
    position: absolute;
    left: 0;
    right: 0;
    top: 368px;
    height: 64px;
    background: var(--brand);
    color: var(--on-brand);
    display: flex;
    flex-direction: column;
    justify-content: center;
    align-items: flex-end;
    padding-right: 34px;
    box-sizing: border-box;
    font-size: 16px;
    line-height: 1.45;
  }
  .info-band__address { letter-spacing: 1.2px; }
  .info-band__lines { letter-spacing: 0.6px; }
</style>
</head>
<body>
  <div class="card">
    <div class="card__decor" role="img" aria-label="Large faint grey interlocking-wheel decoration"></div>

    <div class="brand">
      <span class="brand__mark"></span>
      <span class="brand__name">Torvalen Tools</span>
    </div>

    <div class="contact-person">
      <p class="contact-person__name">Marianne</p>
      <p class="contact-person__mobile">Mo 65-63920457</p>
    </div>

    <div class="info-band">
      <span class="info-band__address">27 Kallang Way #03-12, Brightline Industrial Hub, Singapore 349210</span>
      <span class="info-band__lines">Tel: 65-63920457 | Fax: 65-63920458 | Email: sales@torvalen.com.sg</span>
    </div>
  </div>
</body>
</html>
```